Harborline Lending and Capital. We provide MOSTLY residential home mortgages in Florida AND commercial loans for investment properties throughout the United states.
I would love to emulate so of the lender sites that are available on the internet but I would like to have the site as popular as possible for SEO purposes. Clients can already click the link to take them to the mortgage application where they can complete that and upload documents. If you could polish that up for me that would be great. I can also provide you with great detail on loan programs that are currently being offered. WE OFFER ALL MORTGAGE LENDING PRODUCTS. I would also like to add something in reference to the rate but I don't think it's legal to actually state or promise a rate for mortgage since they vary based on loan type, client and other criteria...

On the Harborline real estate site I would like to add a link or some way for clients to be able to put in credit card information to render services ...

Please let me know what you need from me

Thank you !!

Current link to site to improve and code

https://harborlinelendingandcapital.example/

Industry/Entity Type

Residential and commmercial lending

Coding

Coded - Design and coding required

Number of Pages Required

2 page

Requirements
Must have
• Love to integrate Mortgage interest rates even if general
Nice to have
• Link to fill out mortgage application via Quorvel LPX software

```html
<!DOCTYPE html>
<html lang="en">
<head>
<meta charset="utf-8">
<title>Harborline Lending and Capital</title>
<link href="https://fonts.googleapis.com/css2?family=Lato:wght@400;700;900&family=Montserrat:wght@700&display=swap" rel="stylesheet">
<style>
:root{
  --green-dark:#1f3a1c;
  --green:#8cb83c;
  --green-soft:#9bc24a;
  --ink:#222;
  --muted:#555;
  --field:#e9e9e9;
  --black:#050505;
}
*{box-sizing:border-box;margin:0;padding:0}
html,body{width:1200px;height:4060px;overflow:hidden}
body{position:relative;font-family:"Lato",sans-serif;color:var(--ink);background:#fff}
.abs{position:absolute}
.btn{position:absolute;display:flex;align-items:center;justify-content:center;background:var(--green);color:#fff;font-weight:700;font-size:15px;border-radius:3px;text-decoration:none}
.accent{color:var(--green)}

/* hero */
.hero{left:0;top:0;width:1200px;height:684px;background:linear-gradient(180deg,#fbfaf6 0%,#f8efe4 35%,#f3d6bb 55%,#e6b48f 60%);border-radius:0 0 56px 56px;overflow:hidden}
.brand{left:113px;top:18px;display:flex;align-items:center;gap:14px}
.brand-mark{width:48px;height:48px;border-radius:50%;background:var(--green-dark)}
.brand-name{font-family:"Montserrat",sans-serif;font-weight:700;font-size:13px;color:var(--green-dark);letter-spacing:.3px;line-height:1.9}
.brand-name small{display:block;font-size:10px;letter-spacing:5px;color:var(--green-dark)}
.nav{left:692px;top:19px;display:flex;gap:0;align-items:center}
.nav a{font-size:15px;color:#444;text-decoration:none;padding:10px 14px}
.nav a.active{background:var(--green);color:#fff;font-weight:700;border-radius:3px;margin-right:30px}
.nav a + a{margin-right:30px}
.hero-title{left:0;top:140px;width:1200px;text-align:center;font-weight:700;font-size:42px;line-height:52px;color:var(--green-dark);letter-spacing:-.5px}
.hero-sub{left:0;top:257px;width:1200px;text-align:center;font-size:20px;line-height:26px;color:#333}
.hero-cta{left:403px;top:329px;width:393px;height:43px;font-size:15px}
.hero-photo{left:0;top:378px;width:1200px;height:306px;background:linear-gradient(180deg,#c9846a 0%,#8a6a58 30%,#7b8190 60%,#5d6670 100%)}

/* section headings */
.h2{left:0;width:1200px;text-align:center;font-weight:700;font-size:42px;color:var(--green-dark)}

/* loan programs */
.card{width:307px;top:840px}
.card-photo{width:307px;height:190px;border-radius:2px}
.card-head{display:flex;gap:20px;margin-top:26px;align-items:flex-start}
.card-icon{width:42px;height:42px;background:var(--green);border-radius:4px;flex:none;display:flex;align-items:center;justify-content:center}
.card-title{font-size:20px;line-height:26px;color:var(--green-dark);font-weight:400}
.card-text{margin-top:20px;font-size:14.5px;line-height:22px;color:#333;padding-left:3px}
.card-rule{margin-top:24px;height:2px;background:var(--green)}

/* about */
.about-photo{left:0;top:1303px;width:500px;height:511px;border-radius:0 36px 36px 0;background:linear-gradient(160deg,#a9cbe3 0%,#6f8fa8 35%,#2e4a5e 65%,#6c8a3a 100%)}
.about-title{left:599px;top:1352px;font-weight:700;font-size:42px;line-height:48px;color:var(--green-dark)}
.about-text{left:600px;top:1475px;width:490px;font-size:16px;line-height:25.8px;color:#555}
.about-btn{left:600px;top:1715px;width:154px;height:41px}

/* offer band */
.offer{left:43px;top:1902px;width:1113px;height:391px;border-radius:6px;background:linear-gradient(180deg,#95bd45 0%,#8cb83c 60%,#86b337 100%);text-align:center;color:#fff}
.offer h2{margin-top:74px;font-size:42px;font-weight:700}
.offer h3{margin-top:10px;font-size:22px;font-weight:400}
.offer p{margin:16px auto 0;width:700px;font-size:17.5px;line-height:26px}
.offer .btn{position:static;display:inline-flex;margin-top:26px;width:205px;height:41px;background:var(--green-dark);font-size:15px}

/* properties */
.prop{width:308px;height:241px}
.prop-feature{left:463px;top:2739px;width:275px;height:210px;background:rgba(140,184,60,.92);border-radius:4px;color:#fff;text-align:center;padding-top:56px}
.prop-feature .street{font-size:20px;font-weight:700}
.prop-feature .label{font-size:19px;margin-top:8px}
.prop-feature .rate{font-size:30px;font-weight:700;margin-top:12px}

/* contact */
.contact-title{left:112px;top:3105px;font-size:44px;font-weight:700;color:var(--green-dark)}
.contact-sub{left:112px;top:3178px;font-size:16px;color:#555}
.field{position:absolute;background:var(--field);border-radius:3px;font-size:13px;color:#555;padding:14px 16px}
.contact-photo{left:700px;top:3045px;width:500px;height:509px;border-radius:32px 0 0 32px;background:linear-gradient(135deg,#e3e4e6 0%,#c6c2bd 45%,#8d7d70 75%,#3f4448 100%)}

/* footer */
.footer{left:0;top:3642px;width:1200px;height:418px;background:var(--black);border-radius:48px 48px 0 0;color:#fff}
.fcol{position:absolute;top:76px}
.fcol h4{font-size:21px;font-weight:700;margin-bottom:26px}
.fcol p,.fcol a{display:block;font-size:15px;line-height:26px;color:#fff;text-decoration:none}
.fcol a{margin-bottom:17px;line-height:26px}
.fcontact{display:flex;gap:22px;margin-bottom:18px;font-size:15px;line-height:26px}
.fcontact svg{flex:none;margin-top:5px}
.social{display:flex;gap:16px;margin-top:30px}
.social span{width:34px;height:34px;border-radius:50%;background:#fff}
.social span:first-child{background:var(--green);border-radius:4px}
.frule{left:112px;top:358px;width:976px;height:1px;background:#333}
.copyright{left:0;top:383px;width:1200px;text-align:center;font-size:13px;color:#fff}
</style>
</head>
<body>

<header class="abs hero">
  <div class="abs brand">
    <span class="brand-mark"></span>
    <div class="brand-name">HARBORLINE LENDING AND CAPITAL OF FLORIDA<small>BUSINESS AND COMMERCIAL DIVISION</small></div>
  </div>
  <nav class="abs nav">
    <a class="active" href="#">Home</a><a href="#">About</a><a href="#">Properties</a><a href="#">Contact</a>
  </nav>
  <h1 class="abs hero-title">YOUR BEST RESOURCE FOR HASSLE-FREE,<br>LOW COST MORTGAGE ORIGINATION</h1>
  <p class="abs hero-sub">Residential Home Loans In Florida And Commercial<br>Lending In America</p>
  <a class="btn hero-cta" href="#">Fill Out Mortgage Application To Begin Lending Pr</a>
  <div class="abs hero-photo" role="img" aria-label="Aerial view of a suburban neighborhood of rowhouses with autumn trees"></div>
</header>

<h2 class="abs h2" style="top:757px">Our Loan <span class="accent">Programs</span></h2>

<article class="abs card" style="left:112px">
  <div class="card-photo" role="img" aria-label="Handshake over a desk with a small model house" style="background:linear-gradient(135deg,#5a4030,#c9b39a 55%,#7a5a40)"></div>
  <div class="card-head"><span class="card-icon"><svg width="24" height="24" viewBox="0 0 24 24" fill="none" stroke="#fff" stroke-width="1.8"><path d="M3 11l9-7 9 7v9H3z"/><path d="M10 20v-5h4v5"/></svg></span><h3 class="card-title">Residential Loan<br>Programs</h3></div>
  <p class="card-text">Excepteur sint occaecat cupidatat non proident, sunt in culpa qui officia deserunt mollit anim id est laborum."</p>
  <div class="card-rule"></div>
</article>

<article class="abs card" style="left:446px">
  <div class="card-photo" role="img" aria-label="Loan officer meeting with clients in a bright office" style="background:linear-gradient(135deg,#b8c2c8,#e6e4de 50%,#6f7478)"></div>
  <div class="card-head"><span class="card-icon"><svg width="24" height="24" viewBox="0 0 24 24" fill="none" stroke="#fff" stroke-width="1.8"><rect x="4" y="4" width="16" height="17"/><path d="M8 8h2M14 8h2M8 12h2M14 12h2M8 16h2M14 16h2"/></svg></span><h3 class="card-title">Commercial Loan<br>Programs</h3></div>
  <p class="card-text">Excepteur sint occaecat cupidatat non proident, sunt in culpa qui officia deserunt mollit anim id est laborum."</p>
  <div class="card-rule" style="width:126px"></div>
</article>

<article class="abs card" style="left:780px">
  <div class="card-photo" role="img" aria-label="Hand placing wooden blocks with finance symbols on a blue background" style="background:linear-gradient(135deg,#0a7a94,#12a3c2 50%,#064b66)"></div>
  <div class="card-head"><span class="card-icon"><svg width="24" height="24" viewBox="0 0 24 24" fill="none" stroke="#fff" stroke-width="1.8"><circle cx="12" cy="10" r="6"/><path d="M8 15l-2 6 6-3 6 3-2-6"/></svg></span><h3 class="card-title">Specialized Loan<br>Products</h3></div>
  <p class="card-text">Excepteur sint occaecat cupidatat non proident, sunt in culpa qui officia deserunt mollit anim id est laborum."</p>
  <div class="card-rule" style="width:126px"></div>
</article>

<section>
  <div class="abs about-photo" role="img" aria-label="Modern apartment building with balconies under a blue sky"></div>
  <h2 class="abs about-title">About Harborline <span class="accent">Mortgage</span><br><span class="accent">and Finance</span></h2>
  <p class="abs about-text">Harborline Lending Originates Residential Home loans in Florida and Commercial and business financing in all 50 States. We have over 25 years of experience in ALL types of real estate and commercial lending. We are strategically partnered to help you obtain ALL necessary components of residential and commercial lending. From the RIGHT lending partners to the best practice Insurance avenues and commercial and residential real estate partners</p>
  <a class="btn about-btn" href="#">Read More</a>
</section>

<section class="abs offer">
  <h2>We Offer All Mortgage Lending Products</h2>
  <h3>Your One-Stop Solution for Home and Commercial Financing</h3>
  <p>From first-time homebuyers to seasoned investors, we provide a full range of mortgage products tailored to meet your unique needs. Whether you're purchasing, refinancing, or investing, we have the perfect loan for you.</p>
  <a class="btn" href="#">Explore Our Offerings</a>
</section>

<h2 class="abs h2" style="top:2368px">Our Exclusive <span class="accent">Properties</span></h2>
<div class="abs prop" style="left:112px;top:2454px;background:linear-gradient(180deg,#cfdbe6,#9a5a3a 50%,#6d8a3f)" role="img" aria-label="Modern house with wood cladding and lawn"></div>
<div class="abs prop" style="left:446px;top:2454px;background:linear-gradient(180deg,#8a7a6a,#4a4440 50%,#b8b0a4)" role="img" aria-label="Contemporary two-storey home with dark trim"></div>
<div class="abs prop" style="left:780px;top:2454px;background:linear-gradient(135deg,#dfe1e3,#b9bcbf 55%,#2a2a2a)" role="img" aria-label="Minimal white facade with large windows"></div>
<div class="abs prop" style="left:112px;top:2723px;background:linear-gradient(180deg,#d7dde3,#a2835f 55%,#8c8c86)" role="img" aria-label="Modern building with patterned facade and patio furniture"></div>
<div class="abs prop" style="left:446px;top:2723px;background:linear-gradient(180deg,#b0a090,#6a5646)" role="img" aria-label="Home exterior"></div>
<div class="abs prop" style="left:780px;top:2723px;background:linear-gradient(180deg,#9fc0d8,#5d7a4a 35%,#8a8a86 70%,#b8b4ac)" role="img" aria-label="Single-storey house with garage and driveway"></div>
<div class="abs prop-feature">
  <div class="street">34 Union Avenue</div>
  <div class="label">Mortgage Interest Rates</div>
  <div class="rate">15%</div>
</div>

<section>
  <h2 class="abs contact-title">Get in <span class="accent">Touch</span></h2>
  <p class="abs contact-sub">Please send me a message for general inquiries or reservations.</p>
  <div class="field" style="left:112px;top:3223px;width:244px;height:41px">First Name</div>
  <div class="field" style="left:367px;top:3223px;width:245px;height:41px">Last Name</div>
  <div class="field" style="left:112px;top:3283px;width:244px;height:41px">Email</div>
  <div class="field" style="left:367px;top:3283px;width:245px;height:41px">Phone</div>
  <div class="field" style="left:112px;top:3340px;width:500px;height:85px">Message</div>
  <a class="btn" href="#" style="left:112px;top:3442px;width:153px;height:41px">Send Message</a>
  <div class="abs contact-photo" role="img" aria-label="Hands typing on a laptop while holding a smartphone"></div>
</section>

<footer class="abs footer">
  <div class="fcol" style="left:112px;width:240px">
    <h4>About Us</h4>
    <p>Harborline Lending Originates Residential Home loans in Florida and Commercial and business financing in all 50 States.</p>
    <div class="social"><span></span><span></span><span></span></div>
  </div>
  <div class="fcol" style="left:423px">
    <h4>Main Links</h4>
    <a href="#">Home</a><a href="#">About Us</a><a href="#">Properties</a><a href="#">Contact Us</a>
  </div>
  <div class="fcol" style="left:637px;width:260px">
    <h4>Contact Us</h4>
    <div class="fcontact"><svg width="18" height="18" viewBox="0 0 24 24" fill="none" stroke="#fff" stroke-width="1.8"><path d="M12 22s7-7 7-12a7 7 0 0 0-14 0c0 5 7 12 7 12z"/><circle cx="12" cy="10" r="2.5"/></svg><span>48 Tidewater Row, Harborline Lending and Capital, Florida 32901</span></div>
    <div class="fcontact"><svg width="18" height="18" viewBox="0 0 24 24" fill="none" stroke="#fff" stroke-width="1.8"><path d="M5 3h4l2 5-3 2a12 12 0 0 0 6 6l2-3 5 2v4a2 2 0 0 1-2 2A17 17 0 0 1 3 5a2 2 0 0 1 2-2z"/></svg><span>+1 555 014 2290</span></div>
    <div class="fcontact"><svg width="18" height="18" viewBox="0 0 24 24" fill="none" stroke="#fff" stroke-width="1.8"><rect x="3" y="5" width="18" height="14"/><path d="M3 6l9 7 9-7"/></svg><span>info@harborlinelending.example</span></div>
  </div>
  <div class="fcol" style="left:957px">
    <h4>Other Links</h4>
    <a href="#">Interest rates</a><a href="#">Support</a><a href="#">Terms &amp; Conditions</a><a href="#">Privacy Policy</a>
  </div>
  <div class="abs frule"></div>
  <p class="abs copyright">Copyright © 2025 &nbsp;Harborline Lending and Capital. All rights reserved.</p>
</footer>

</body>
</html>
```